we need a design for Water Bottle Lable Wrap
The product is called Calmora Springs is a restructured water. its a very healthy and rejuvenating water
we were looking at using as a tag ling Restore, Recover, Rejuvenate.

```html
<!DOCTYPE html>
<html lang="en">
<head>
<meta charset="utf-8">
<title>Calmora Springs – Bottle Label Wrap</title>
<link rel="stylesheet" href="https://fonts.googleapis.com/css2?family=Outfit:wght@600;700;800&display=swap">
<style>
  :root {
    --stage: #333333;
    --green-light: #1ee04f;
    --green-mid: #14a534;
    --green-dark: #0c5f1d;
    --navy-dark: #14265a;
    --navy-mid: #27478f;
    --teal-light: #4fa8c9;
    --band-dark: #0a1a66;
    --band-mid: #1e3fa8;
    --band-light: #2f63d2;
    --ink-blue: #1a2f9a;
    --white: #ffffff;
    --drop: #37b7f0;
    --sky: #8fb8d8;
    --meadow: #4f8a2a;
    --forest: #2f5e22;
    --snow: #d9e4ef;
    --lake: #4aa0d8;
    --lake-deep: #3b86c4;
  }
  * { box-sizing: border-box; margin: 0; padding: 0; }
  html, body {
    width: 1200px; height: 745px; overflow: hidden;
    background: var(--stage);
    font-family: "Outfit", "Poppins", sans-serif;
  }
  .stage {
    position: relative; width: 1200px; height: 745px;
    display: flex; justify-content: center; align-items: center; gap: 80px;
  }
  .label {
    position: relative; width: 470px; height: 438px;
    display: flex; flex-direction: column; overflow: hidden;
  }
  .brand-panel {
    position: relative; height: 198px;
    display: flex; flex-direction: column; align-items: center; justify-content: center; gap: 18px;
  }
  .label--green .brand-panel {
    background: radial-gradient(ellipse at 55% 10%, var(--green-light) 0%, var(--green-mid) 45%, var(--green-dark) 100%);
  }
  .label--blue .brand-panel {
    background: linear-gradient(115deg, var(--navy-dark) 0%, var(--navy-mid) 55%, var(--teal-light) 100%);
  }
  .brand-dot {
    width: 52px; height: 52px; border-radius: 50%;
    background: var(--drop);
  }
  .brand-name {
    font-weight: 700; font-size: 40px; letter-spacing: 1px;
    color: var(--white); text-transform: uppercase; line-height: 1;
  }
  .tagline-band {
    height: 54px;
    display: flex; align-items: center; justify-content: center;
    background: linear-gradient(90deg, var(--band-dark) 0%, var(--band-mid) 45%, var(--band-light) 70%, var(--band-dark) 100%);
    border-top: 2px solid var(--white);
    border-bottom: 2px solid var(--white);
  }
  .tagline {
    font-weight: 700; font-size: 24px; color: var(--white);
    letter-spacing: 0.3px; white-space: nowrap;
  }
  .scene-panel {
    position: relative; flex: 1;
  }
  .scene-art {
    position: absolute; inset: 0;
    background: linear-gradient(180deg, var(--meadow) 0%, var(--forest) 18%, var(--snow) 40%, var(--sky) 52%, var(--lake) 75%, var(--lake-deep) 100%);
  }
  .product-type,
  .volume {
    position: absolute;
    font-weight: 800; color: var(--white); line-height: 1.15;
    text-shadow:
      2px 0 0 var(--ink-blue), -2px 0 0 var(--ink-blue),
      0 2px 0 var(--ink-blue), 0 -2px 0 var(--ink-blue),
      1.5px 1.5px 0 var(--ink-blue), -1.5px -1.5px 0 var(--ink-blue),
      1.5px -1.5px 0 var(--ink-blue), -1.5px 1.5px 0 var(--ink-blue);
  }
  .product-type {
    left: 25px; bottom: 16px;
    font-size: 27px;
  }
  .volume {
    right: 22px; bottom: 28px;
    font-size: 22px;
  }
</style>
</head>
<body>
<main class="stage">
  <section class="label label--green">
    <div class="brand-panel">
      <span class="brand-dot"></span>
      <span class="brand-name">Calmora Springs</span>
    </div>
    <div class="tagline-band"><p class="tagline">RESTORE, RECOVER, REJUVENATE</p></div>
    <div class="scene-panel">
      <div class="scene-art" role="img" aria-label="Snow-capped mountain peak between green forested valleys, reflected in a clear blue alpine lake"></div>
      <p class="product-type">Restructured<br>Water</p>
      <p class="volume">600ML</p>
    </div>
  </section>

  <section class="label label--blue">
    <div class="brand-panel">
      <span class="brand-dot"></span>
      <span class="brand-name">Calmora Springs</span>
    </div>
    <div class="tagline-band"><p class="tagline">RESTORE, RECOVER, REJUVENATE</p></div>
    <div class="scene-panel">
      <div class="scene-art" role="img" aria-label="Snow-capped mountain peak between green forested valleys, reflected in a clear blue alpine lake"></div>
      <p class="product-type">Restructured<br>Water</p>
      <p class="volume">600ML</p>
    </div>
  </section>
</main>
</body>
</html>
```